RW Holloway LLC Business Card - Civil Engineering & Consulting Firm

We need a Business Card that is elegant, and masculine.  It is our Professional Civil Engineering & Consulting Company located in San Antonio TX (Not s construction or builder firm- no gears & no tool images please). We provide civil engineering services including  commercial site plans, grading and drainage plans, utility plans, hydraulics and hydrology, land planning, utility coordination, and other general civil engineering services related to commercial and residential development.
We have 2 existing Logos. We would like to convey reliability, strength, trustworthiness and attention to detail.  Blues and orange tones as per logo We are OK with the use of a darker blue in the mix.  We have 2 logo versions - Full Company Name Logo to go on the back of card, & Small Icon Logo for the front w/ personal Info.

Target Market(s)
Architects, Real Estate Developers, Other Strctural Engineers, Surveyers, General Contractors
Industry/Entity Type
Professional Civil Engineering
Contact Information for Business Card
Name, Position, Address, Cell & Office #, email, and company website
Font styles to use
Other font styles liked:
- Avian
Requirements
Should not have
- No Tools, No Gears, no Cranes, or Construction Equipment.

```html
<!DOCTYPE html>
<html lang="en">
<head>
<meta charset="utf-8">
<title>RW Holloway LLC – Business Card</title>
<link rel="stylesheet" href="https://fonts.googleapis.com/css2?family=Montserrat:wght@400;500;700&family=Josefin+Sans:wght@300;400&display=swap">
<style>
  :root {
    --stage: #262626;
    --sky: #7aaed8;
    --amber: #ef9430;
    --amber-soft: #dc9a5c;
    --ink: #1c1c1c;
    --paper: #ffffff;
    --paper-shade: #ececec;
  }
  * { margin: 0; padding: 0; box-sizing: border-box; }
  html, body { width: 1200px; height: 900px; overflow: hidden; }
  body {
    background: var(--stage);
    font-family: "Montserrat", sans-serif;
    position: relative;
  }
  .card {
    position: absolute;
    width: 640px;
    height: 366px;
    overflow: hidden;
    box-shadow: 0 10px 30px rgba(0,0,0,.45);
  }
  /* Brand side */
  .card--brand {
    left: 280px;
    top: 60px;
    background: linear-gradient(180deg, var(--sky) 0%, #a7a7a7 50%, var(--amber-soft) 100%);
    display: flex;
    flex-direction: column;
    align-items: center;
    justify-content: center;
    color: var(--paper);
    padding: 0 40px;
  }
  .brand-name {
    font-family: "Josefin Sans", sans-serif;
    font-weight: 300;
    font-size: 46px;
    letter-spacing: 3px;
    text-transform: uppercase;
    white-space: nowrap;
  }
  .brand-rule {
    width: 440px;
    height: 2px;
    background: var(--paper);
    margin-top: 10px;
  }
  .brand-tagline {
    font-family: "Josefin Sans", sans-serif;
    font-weight: 300;
    font-size: 16px;
    letter-spacing: 9px;
    text-transform: uppercase;
    white-space: nowrap;
    margin-top: 14px;
  }
  /* Contact side */
  .card--contact {
    left: 280px;
    top: 474px;
    background: linear-gradient(135deg, var(--paper-shade) 0%, var(--paper) 45%, var(--paper) 70%, var(--paper-shade) 100%);
  }
  .person { position: absolute; left: 44px; top: 30px; color: var(--ink); }
  .person-name {
    color: var(--amber);
    font-weight: 700;
    font-size: 24px;
    letter-spacing: 1px;
    text-transform: uppercase;
    line-height: 1.2;
  }
  .person-role { font-size: 16px; margin-top: 2px; line-height: 1.3; }
  .address { font-size: 16px; line-height: 1.3; margin-top: 12px; }
  .contact-list { list-style: none; margin-top: 10px; }
  .contact-list li {
    display: flex;
    align-items: center;
    gap: 12px;
    font-size: 16px;
    line-height: 1.45;
  }
  .contact-list svg { width: 17px; height: 17px; fill: var(--amber); flex: none; }
  .mark {
    position: absolute;
    right: 52px;
    top: 140px;
    display: flex;
    align-items: center;
    gap: 10px;
    color: var(--sky);
    font-weight: 500;
    font-size: 22px;
  }
  .mark-square { width: 18px; height: 18px; background: var(--amber); }
  .wave { position: absolute; left: 0; bottom: 0; width: 640px; height: 96px; }
</style>
</head>
<body>

<section class="card card--brand" aria-label="Card back">
  <div class="brand-name">RW Holloway LLC</div>
  <div class="brand-rule"></div>
  <div class="brand-tagline">Consulting Engineers</div>
</section>

<section class="card card--contact" aria-label="Card front">
  <div class="person">
    <div class="person-name">Daniel Whitford</div>
    <div class="person-role">Co-Founder</div>
    <div class="address">4180 N. Briar Ridge Road<br>Suite 210 San Antonio</div>
    <ul class="contact-list">
      <li>
        <svg viewBox="0 0 24 24" aria-hidden="true"><path d="M6.6 10.8a15 15 0 0 0 6.6 6.6l2.2-2.2a1 1 0 0 1 1-.25 11.4 11.4 0 0 0 3.6.57 1 1 0 0 1 1 1V20a1 1 0 0 1-1 1A17 17 0 0 1 3 4a1 1 0 0 1 1-1h3.5a1 1 0 0 1 1 1c0 1.25.2 2.45.57 3.57a1 1 0 0 1-.25 1z"/></svg>
        210-555-0148
      </li>
      <li>
        <svg viewBox="0 0 24 24" aria-hidden="true"><path d="M2 7c3-3 17-3 20 0v3h-5V8H7v2H2z"/><rect x="4" y="11" width="16" height="10" rx="1.5"/></svg>
        210-555-0192
      </li>
      <li>
        <svg viewBox="0 0 24 24" aria-hidden="true"><path d="M2 5h20v14H2z M3 6l9 7 9-7" stroke="#fff" stroke-width="1.5"/></svg>
        info@rwhollowayllc
      </li>
      <li>
        <svg viewBox="0 0 24 24" aria-hidden="true"><circle cx="12" cy="12" r="10"/><path d="M2 12h20M12 2c3 3 3 17 0 20M12 2c-3 3-3 17 0 20" stroke="#fff" stroke-width="1.2" fill="none"/></svg>
        www.hollowaycivil.com
      </li>
    </ul>
  </div>

  <div class="mark"><span class="mark-square"></span>RW Holloway LLC</div>

  <svg class="wave" viewBox="0 0 640 96" preserveAspectRatio="none" aria-hidden="true">
    <defs>
      <linearGradient id="waveFill" x1="0" y1="0" x2="0" y2="1">
        <stop offset="0" stop-color="#7aaed8"/>
        <stop offset="0.55" stop-color="#c9a98a"/>
        <stop offset="1" stop-color="#ef9430"/>
      </linearGradient>
    </defs>
    <path d="M0 18 C200 38 420 64 640 70 L640 96 L0 96 Z" fill="url(#waveFill)"/>
    <path d="M0 24 C200 46 420 72 640 78" stroke="#ffffff" stroke-width="4" fill="none"/>
    <path d="M140 28 C310 46 470 60 640 62" stroke="#7aaed8" stroke-width="4" fill="none"/>
  </svg>
</section>

</body>
</html>
```